Quick Straightforward Billboard Redesign

- Design billboard sized for 10 foot' x 36' foot width live area size and please include bleeds 6" around all sides
- Exact blue color match is imperative in headline, logo, phone number bubble or wherever used. C-83 / M-45 / Y-1 / K-0-
- What I hope to illustrate is that our company offers the best porch screening in the area area, in regards to quality, expertise, durability, storms proof, but we do not build screen porches.
- Current board is attached below from previous designer, and as you can see sizing was off, white space on edges make it appear to be sized incorrectly.
- I also attached my own little mock up idea well well if it helps, favorite image, logo, headline, etc and ideas perhaps on expanding or making this better?

Thanks so much!

Target Market(s)

Drivers and passengers, Southeastern NC, are of immense new construction and high end homes.

Industry/Entity Type

Construction

Colors
0054AA
0677BA
7BADD7
CADEEF
E8F1F8

Requirements
Must have
• Blue color matching
Nice to have
• Design spins or other thoughts on my little mock up

```html
<!DOCTYPE html>
<html lang="en">
<head>
<meta charset="utf-8">
<title>Tidewater Screens Billboard</title>
<link href="https://fonts.googleapis.com/css2?family=Barlow+Condensed:wght@600;800&display=swap" rel="stylesheet">
<style>
  :root {
    --brand-blue: #1a7ac0;
    --deep-blue: #0f6db5;
    --light-blue: #2fb3ec;
    --brand-green: #22a24a;
    --white: #ffffff;
    --canvas: #ffffff;
  }
  html, body {
    margin: 0;
    padding: 0;
    width: 1185px;
    height: 1200px;
    overflow: hidden;
    background: var(--canvas);
  }
  .billboard {
    position: absolute;
    left: 42px;
    top: 448px;
    width: 1100px;
    height: 304px;
    overflow: hidden;
    background: linear-gradient(180deg, var(--white) 0%, var(--white) 85%, #e9ecef 100%);
    box-shadow: 0 10px 18px rgba(0,0,0,0.18);
    font-family: "Barlow Condensed", "Arial Narrow", sans-serif;
  }
  .porch-photo {
    position: absolute;
    left: 620px;
    top: 0;
    width: 480px;
    height: 304px;
    background:
      linear-gradient(90deg, rgba(255,255,255,1) 0%, rgba(255,255,255,0) 32%),
      linear-gradient(180deg, #eef0ee 0%, #e4e6e2 22%, #8fb6d6 38%, #9cc06e 55%, #8d8877 72%, #c9c3b6 100%);
  }
  .graphics {
    position: absolute;
    left: 0;
    top: 0;
  }
  .headline {
    position: absolute;
    left: 31px;
    margin: 0;
    font-weight: 800;
    font-size: 66px;
    line-height: 1;
    letter-spacing: 0.5px;
    text-transform: uppercase;
    white-space: nowrap;
  }
  .headline--white { color: var(--white); }
  .headline--green { color: var(--brand-green); }
  .line-1 { top: 28px; }
  .line-2 { top: 86px; }
  .line-3 { top: 155px; }
  .line-4 { top: 217px; }
  .brand-mark {
    position: absolute;
    left: 402px;
    top: 200px;
    width: 66px;
    height: 66px;
    background: var(--brand-blue);
  }
  .brand-name {
    position: absolute;
    left: 491px;
    top: 176px;
    margin: 0;
    color: var(--deep-blue);
    font-weight: 600;
    font-size: 50px;
    line-height: 52px;
    text-transform: uppercase;
    white-space: nowrap;
  }
  .phone-bar {
    position: absolute;
    left: 789px;
    top: 230px;
    width: 311px;
    height: 49px;
    background: var(--brand-blue);
    box-shadow: 0 3px 5px rgba(0,0,0,0.2);
  }
  .phone-number {
    position: absolute;
    left: 828px;
    top: 231px;
    margin: 0;
    color: var(--white);
    font-weight: 800;
    font-size: 44px;
    line-height: 48px;
    letter-spacing: 1px;
  }
  .phone-badge {
    position: absolute;
    left: 738px;
    top: 220px;
  }
</style>
</head>
<body>
  <div class="billboard">
    <div class="porch-photo" role="img" aria-label="Photo of a screened coastal porch with wicker seating overlooking a lake"></div>

    <svg class="graphics" width="1100" height="304" viewBox="0 0 1100 304" aria-hidden="true">
      <defs>
        <linearGradient id="stripe-fade" x1="1" y1="0" x2="0" y2="1">
          <stop offset="0" stop-color="#22a24a"/>
          <stop offset="1" stop-color="#22a24a" stop-opacity="0"/>
        </linearGradient>
        <linearGradient id="chevron-fade" x1="0" y1="0" x2="1" y2="1">
          <stop offset="0" stop-color="#2fb3ec" stop-opacity="0.9"/>
          <stop offset="1" stop-color="#1a7ac0" stop-opacity="0.2"/>
        </linearGradient>
      </defs>
      <polygon class="blue-band" points="0,0 592,0 382,146 0,146" fill="var(--brand-blue)"/>
      <polygon class="chevron" points="470,0 520,0 560,36 535,58" fill="url(#chevron-fade)" opacity="0.8"/>
      <polygon class="chevron" points="520,0 575,0 515,46 495,30" fill="url(#chevron-fade)" opacity="0.7"/>
      <polygon class="green-stripe" points="620,0 664,0 480,128 436,128" fill="url(#stripe-fade)"/>
    </svg>

    <p class="headline headline--white line-1">Screen</p>
    <p class="headline headline--white line-2">Your Porch.</p>
    <p class="headline headline--green line-3">Built For</p>
    <p class="headline headline--green line-4">The Coast.</p>

    <div class="brand-mark"></div>
    <p class="brand-name">Tidewater<br>Screens</p>

    <div class="phone-bar"></div>
    <svg class="phone-badge" width="70" height="70" viewBox="0 0 70 70" aria-hidden="true">
      <circle cx="35" cy="35" r="33" fill="var(--white)"/>
      <circle cx="35" cy="35" r="29" fill="var(--brand-green)"/>
      <path d="M25 21c2-1 4-1 5 1l3 6c1 2 0 3-1 4l-2 2c2 4 5 7 9 9l2-2c1-1 2-2 4-1l6 3c2 1 2 3 1 5l-2 3c-2 2-5 2-8 1-9-4-16-11-20-20-1-3-1-6 1-8z" fill="var(--white)"/>
    </svg>
    <p class="phone-number">555.014.2281</p>
  </div>
</body>
</html>
```